Business Card Design

I already have a company logo for my company. I have a logo for the manufacturer we represent. I want a professional business card design.

```html
<!DOCTYPE html>
<html lang="en">
<head>
<meta charset="utf-8">
<title>Signal Guard Co – Business Card</title>
<link rel="stylesheet" href="https://fonts.googleapis.com/css2?family=Montserrat:wght@400;500;700&display=swap">
<style>
  :root {
    --bg: #e9e7e4;
    --card: #ffffff;
    --red: #e31e24;
    --ink: #1c1c1c;
    --grey: #4a4a4a;
  }
  * { margin: 0; padding: 0; box-sizing: border-box; }
  html, body { width: 1200px; height: 786px; overflow: hidden; }
  body {
    background: var(--bg);
    font-family: "Montserrat", sans-serif;
    color: var(--ink);
    display: flex;
    align-items: center;
    justify-content: center;
    gap: 60px;
  }
  .card {
    position: relative;
    width: 520px;
    height: 297px;
    background: var(--card);
    box-shadow: 0 6px 18px rgba(0,0,0,0.18);
  }
  .brand {
    display: flex;
    align-items: center;
    gap: 10px;
    font-weight: 700;
    color: var(--red);
    letter-spacing: 0.02em;
    white-space: nowrap;
  }
  .brand-dot {
    width: 14px; height: 14px;
    border-radius: 50%;
    background: var(--red);
    flex: none;
  }
  /* front */
  .card-front .brand {
    position: absolute;
    top: 64px; right: 56px;
    font-size: 24px;
  }
  .divider {
    position: absolute;
    left: 34px; right: 34px; top: 176px;
    height: 1.5px;
    background: var(--red);
  }
  .person {
    position: absolute;
    left: 34px; top: 124px;
  }
  .person-name {
    font-size: 22px;
    font-weight: 700;
    color: var(--red);
    line-height: 1.1;
  }
  .person-title {
    font-size: 12.5px;
    font-weight: 500;
    color: var(--ink);
    margin-top: 2px;
  }
  .contacts {
    position: absolute;
    left: 34px; top: 200px;
    list-style: none;
    font-size: 12.5px;
    line-height: 1.55;
  }
  .contacts li { display: flex; align-items: center; gap: 10px; }
  .contacts svg { width: 11px; height: 11px; fill: var(--red); flex: none; }
  .address {
    position: absolute;
    right: 34px; top: 190px;
    font-size: 12px;
    line-height: 1.4;
    font-style: normal;
  }
  /* back */
  .card-back {
    display: flex;
    align-items: center;
    justify-content: center;
  }
  .card-back .brand { font-size: 32px; }
  .card-back .brand-dot { width: 18px; height: 18px; }
</style>
</head>
<body>
  <section class="card card-front">
    <div class="brand"><span class="brand-dot"></span>Signal Guard Co</div>

    <div class="person">
      <p class="person-name">Daniel Ortiz</p>
      <p class="person-title">Managing Director</p>
    </div>

    <div class="divider"></div>

    <ul class="contacts">
      <li>
        <svg viewBox="0 0 12 12" aria-hidden="true"><path d="M2 1h2.5l1 3-1.5 1a6 6 0 0 0 3 3l1-1.5 3 1V11c0 .5-.5 1-1 1A10 10 0 0 1 0 2c0-.5.5-1 1-1z"/></svg>
        555.210.0147
      </li>
      <li>
        <svg viewBox="0 0 12 12" aria-hidden="true"><path d="M0 2h12v8H0z M0 2l6 4 6-4" fill="none" stroke="#e31e24" stroke-width="1.4"/></svg>
        info@signalguardco.com
      </li>
      <li>
        <svg viewBox="0 0 12 12" aria-hidden="true"><circle cx="6" cy="6" r="6"/></svg>
        www.signalguardco.com
      </li>
    </ul>

    <address class="address">2840 Harlow Ave<br>Lakeview, CO 80000</address>
  </section>

  <section class="card card-back">
    <div class="brand"><span class="brand-dot"></span>Signal Guard Co</div>
  </section>
</body>
</html>
```